Electrician Business Card/ company logo/small business

New Business Cards and logo needed that will catch peoples eye and say we went that extra step. Attached is a design possibly to be incorporated, if u have your own great, lets see it!... This will be a small local business. thank you for all you do!
Halvern Electric
Ned Fosky Owner
Journeyman Electrician
phone 1.555.208.3471
email: KQLHalvernElectric@quellmail.net
call for free estimate!
Updates

Accepted and approved for cards

Target Market(s)

support small local business

Industry/Entity Type

Electrical,

Contact Information for Business Card

name, title,company/ logo, phone, email, free estimate

Other font styles liked:
• easy to read

Colors

Designer to choose colors to be used in the design.

Requirements
Must have
• eye catching everything! logo and halvern electric listed on business card/logo, incorp logo in the background of card
Nice to have
• lightening bolts in eyes or around the triangle? vertical, modern, any design that would be unique and stand out
Should not have
• pinks, reds, yellows,brown

```html
<!DOCTYPE html>
<html lang="en">
<head>
<meta charset="utf-8">
<title>Halvern Electric – Business Card</title>
<link href="https://fonts.googleapis.com/css2?family=Michroma&family=Arimo:wght@400&display=swap" rel="stylesheet">
<style>
  :root {
    --bg: #c9c9c9;
    --card: #1c1c1d;
    --card-deep: #141415;
    --blue: #1f8fe0;
    --blue-edge: #1a78d6;
    --white: #f2f2f2;
    --grey-line: #2e2e30;
  }
  * { box-sizing: border-box; margin: 0; padding: 0; }
  html, body {
    width: 1200px; height: 800px; overflow: hidden;
    background: var(--bg);
  }
  .canvas {
    position: relative; width: 1200px; height: 800px;
    display: flex; align-items: center; justify-content: center; gap: 50px;
  }
  .card {
    position: relative; width: 525px; height: 300px;
    background: var(--card);
    border-bottom: 3px solid var(--blue-edge);
    border-left: 2px solid var(--blue-edge);
    box-shadow: 0 14px 30px rgba(0,0,0,0.28);
    overflow: hidden;
  }
  .wordmark {
    font-family: "Michroma", sans-serif;
    color: var(--blue);
    text-transform: uppercase;
    line-height: 1.15;
  }
  .brand-dot {
    display: inline-block; width: 14px; height: 14px;
    background: var(--blue); margin-right: 14px; vertical-align: middle;
  }

  /* Front */
  .front .brand {
    position: absolute; left: 48px; top: 52px;
    display: flex; align-items: center;
  }
  .front .wordmark { font-size: 30px; letter-spacing: 1px; }
  .front .wordmark .sub { font-size: 19px; letter-spacing: 6px; display: block; margin-left: 30px; }
  .front .divider {
    position: absolute; left: 48px; right: 40px; top: 172px;
    height: 1px; background: var(--blue);
  }
  .front .person { position: absolute; left: 48px; top: 118px; }
  .front .name {
    font-family: "Michroma", sans-serif; color: var(--blue);
    font-size: 20px; text-transform: uppercase; letter-spacing: 1px;
  }
  .front .title {
    font-family: "Arimo", sans-serif; color: var(--white);
    font-size: 15px; margin-top: 2px;
  }
  .front .contact {
    position: absolute; left: 48px; top: 190px;
    font-family: "Arimo", sans-serif; color: var(--white); font-size: 16px;
    display: grid; gap: 8px;
  }
  .contact-row { display: flex; align-items: center; gap: 10px; }
  .contact-row svg { width: 16px; height: 16px; flex: none; }

  /* Back */
  .back { background: var(--card-deep); }
  .back .pattern {
    position: absolute; inset: 0;
    background: radial-gradient(ellipse at 70% 30%, #2a2a2c 0%, #1a1a1b 55%, #111112 100%);
  }
  .back .brand {
    position: absolute; left: 0; right: 0; top: 0; bottom: 0;
    display: flex; align-items: center; justify-content: center;
  }
  .back .wordmark { font-size: 28px; }
  .back .wordmark .sub { font-size: 17px; letter-spacing: 6px; display: block; margin-left: 30px; }
</style>
</head>
<body>
<main class="canvas">

  <section class="card front" aria-label="Business card front">
    <div class="person">
      <p class="name">Ned Fosky</p>
      <p class="title">Journeyman Electrician</p>
    </div>
    <div class="brand">
      <span class="brand-dot"></span>
      <p class="wordmark">Halvern<span class="sub">Electric</span></p>
    </div>
    <div class="divider"></div>
    <div class="contact">
      <div class="contact-row">
        <svg viewBox="0 0 16 16" aria-hidden="true"><path d="M3.5 1.5l2.5 3-1.5 1.5c.8 1.8 2.2 3.2 4 4l1.5-1.5 3 2.5-1.5 2.5C7 13.5 2.5 9 1 3z" fill="var(--blue)"/></svg>
        <span>1.555.208.3471</span>
      </div>
      <div class="contact-row">
        <svg viewBox="0 0 16 16" aria-hidden="true"><rect x="1" y="3" width="14" height="10" fill="var(--blue)"/><path d="M1 3l7 6 7-6" stroke="var(--card)" stroke-width="1.3" fill="none"/></svg>
        <span>KQLHalvernElectric@quellmail.net</span>
      </div>
    </div>
  </section>

  <section class="card back" aria-label="Business card back">
    <div class="pattern" role="img" aria-label="Repeating tone-on-tone embossed brand pattern across the card"></div>
    <div class="brand">
      <span class="brand-dot"></span>
      <p class="wordmark">Halvern<span class="sub">Electric</span></p>
    </div>
  </section>

</main>
</body>
</html>
```